Design Website Templates for Photographers for Lumera Inc. (trylumera.example)

Lumera Inc. is a generative website company for wedding photographers.
We are seeking new photography website design inspirations for the next template to be offered on our platform. The catch is you must use the same data for your designs. You also must use all of the data somewhere in the design. You cannot add new content besides the data available. If you wish to add any elements It will be hardcoded and must be universally fitting for many different photographers. We recommend not using any hardcoded test.
Don't be afraid to be creative! Although the most important element of a photographers website is the photos, we are looking for unique and out-of-the-box designs for the actual site as well.
Here is the User generated data available to you:
- 4 Hero Images Landscape, 4 Hero Images Portrait
- Tagline “destination photographer based in Maui, Hawaii”
- “About Photo” of the photographer
- “About” Biography Text
- The design can use up to 3 colors + background color and 2 fonts
- 9 Gallery images
- 3 Packages/services that include landscape/portrait images, a price, a title and text
- Testimonials made up of an image, text and text for the name of testimonial giver
See some examples of our current website designs attached. You can use any of the data you see in the designs.
Updates
We are looking for designs that are less feminine and are more neutral in color and fonts. Currently our templates are more oriented towards feminine photographers. We want to have designs that speak to diverse audiences. We thank everyone for submitting and are reviewing the designs.
Number of Pages Required
1 page
Look and feel
Each slider illustrates characteristics of the customer's brand and the style your logo design should communicate.

```html
<!DOCTYPE html>
<html lang="en">
<head>
<meta charset="utf-8">
<title>Lumera — Wedding Photography</title>
<link href="https://fonts.googleapis.com/css2?family=Poppins:wght@400;500;600;700;800&display=swap" rel="stylesheet">
<style>
:root{
  --brown-dark:#4a2318;
  --brown:#a26a4c;
  --brown-frame:#7d4536;
  --gold:#dba233;
  --cream:#f1e7e0;
  --cream-light:#f7f4f1;
  --ink:#2c1a14;
  --footer:#2b2b2b;
  --white:#ffffff;
}
*{margin:0;padding:0;box-sizing:border-box}
html,body{width:1200px;height:5089px;overflow:hidden}
body{font-family:'Poppins',sans-serif;color:var(--ink);position:relative;background:var(--cream-light)}
.abs{position:absolute}
.photo{position:absolute;display:block}
.btn{position:absolute;background:var(--gold);color:var(--brown-dark);font-weight:600;font-size:16px;display:flex;align-items:center;justify-content:center;letter-spacing:.3px}
.section-title{position:absolute;font-weight:700;color:var(--brown-dark);font-size:38px;letter-spacing:.5px}
.body-text{position:absolute;font-size:15px;line-height:30px;color:var(--ink);text-align:justify}

/* hero */
.hero{position:absolute;left:0;top:0;width:1200px;height:664px;background:linear-gradient(100deg,#c98a54 0%,#d49a62 40%,#c88750 75%,#b97a48 100%)}
.hero-couple{left:60px;top:60px;width:440px;height:604px;background:linear-gradient(180deg,#3a3230,#6d5a52 55%,#d8ccc4 80%,#e6ddd6)}
.hero-veil{left:520px;top:120px;width:600px;height:520px;background:radial-gradient(ellipse at 60% 40%,rgba(255,255,255,.35),rgba(255,255,255,0) 70%)}
.nav{position:absolute;left:0;top:0;width:1200px;height:75px;background:rgba(60,35,25,.55);display:flex;align-items:center}
.logo{position:absolute;color:var(--white);font-weight:600;letter-spacing:2px}
.nav .logo{left:60px;top:17px;font-size:32px}
.nav-links{position:absolute;left:281px;top:0;height:75px;display:flex}
.nav-links a{color:var(--white);text-decoration:none;font-weight:600;font-size:15px;height:75px;display:flex;align-items:center;padding:0 22px}
.nav-links a.active{background:var(--gold);width:101px;justify-content:center;padding:0}
.hero-title{left:548px;top:282px;font-size:82px;line-height:78px;font-weight:800;color:var(--brown-dark);letter-spacing:1px}

/* about photo */
.about-photo{position:absolute;left:0;top:664px;width:1200px;height:621px;background:radial-gradient(ellipse at 75% 50%,#efe3d6,#f3ece6 60%,#f5efea)}
.framed{position:absolute;border:4px solid var(--brown-frame)}

/* gallery */
.gallery{position:absolute;left:0;top:1285px;width:1200px;height:1320px;background:var(--brown)}

/* about me */
.about-me{position:absolute;left:0;top:2605px;width:1200px;height:588px;background:var(--cream)}
.about-me .halo{left:200px;top:2700px;width:380px;height:420px;border-radius:50%;background:radial-gradient(circle,#f3d9a8 0%,rgba(241,231,224,0) 70%)}

/* packages */
.packages{position:absolute;left:0;top:3193px;width:1200px;height:899px;background:linear-gradient(160deg,#f6f6f8,#eeeef2 60%,#f7f7f9)}
.pkg-label{position:absolute;width:308px;text-align:center;color:var(--gold);font-weight:600;font-size:20px}
.price{position:absolute;width:158px;height:55px;border:2px solid var(--brown-frame);display:flex;align-items:center;justify-content:center;font-weight:700;font-size:32px;color:var(--brown-dark);background:var(--white)}
.pkg-text{position:absolute;width:260px;text-align:center;font-size:14px;line-height:29px}

/* testimonials */
.testimonials{position:absolute;left:0;top:4092px;width:1200px;height:720px;background:linear-gradient(150deg,#f3efea,#ebe6e0 50%,#f4f0eb)}
.card-bg{left:297px;top:4270px;width:573px;height:421px;background:linear-gradient(180deg,#b9a193 0%,#e0b48f 45%,#a8826a 70%,#5c4538 100%)}
.quote-box{position:absolute;left:352px;top:4464px;width:459px;height:186px;background:#9a5a3e;border-radius:22px;color:var(--white)}
.avatar{left:508px;top:4355px;width:146px;height:146px;border-radius:50%;background:linear-gradient(180deg,#d9a374,#b57b55);border:5px solid var(--white)}
.see-more{left:901px;top:4660px;font-size:19px;color:var(--brown-dark);text-decoration:underline;display:flex;align-items:center;gap:10px}

/* footer */
.footer{position:absolute;left:0;top:4812px;width:1200px;height:277px;background:var(--footer)}
.footer-nav{position:absolute;left:0;top:4812px;width:1200px;height:60px;display:flex;justify-content:center;gap:0;border-bottom:1px solid #3d3d3d}
.footer-nav a{color:var(--white);text-decoration:none;font-weight:600;font-size:15px;display:flex;align-items:center;padding:0 18px}
.footer .logo{left:0;width:1200px;text-align:center;top:85px;font-size:56px}
.socials{position:absolute;left:0;top:4996px;width:1200px;display:flex;justify-content:center;gap:24px}
.socials span{width:18px;height:18px;border-radius:50%;background:var(--white)}
.copyright{position:absolute;left:0;top:5057px;width:1200px;text-align:center;color:var(--white);font-size:14px}
</style>
</head>
<body>

<!-- Hero -->
<section class="hero">
  <div class="photo hero-couple" role="img" aria-label="Bride and groom posing against a warm stone wall"></div>
  <div class="photo hero-veil" role="img" aria-label="Flowing wedding veil"></div>
</section>
<header class="nav">
  <div class="logo">LUMERA</div>
  <nav class="nav-links">
    <a class="active">HOME</a><a>ABOUT PHOTO</a><a>GALLERY</a><a>ABOUT ME</a><a>PACKAGES</a><a>CONTACT US</a>
  </nav>
</header>
<h1 class="abs hero-title">WELCOME TO<br>LUMERA</h1>
<div class="btn" style="left:553px;top:470px;width:194px;height:52px">BOOK NOW</div>

<!-- About Photo -->
<section class="about-photo"></section>
<h2 class="section-title" style="left:358px;top:772px">ABOUT PHOTO</h2>
<p class="body-text" style="left:156px;top:852px;width:486px">Lorem ipsum dolor sit amet, consectetur adipiscing elit, sed do eiusmod tempor incididunt ut labore et dolore magna aliqua. Ut enim ad minim veniam, quis nostrud exercitation ullamco laboris nisi ut aliquip ex ea commodo consequat. Duis aute irure dolor in reprehenderit in voluptate velit esse cillum dolore eu fugiat nulla pariatur. Excepteur sint occaecat cupidatat non proident, sunt in culpa qui officia deserunt mollit anim id est laborum</p>
<div class="btn" style="left:441px;top:1127px;width:194px;height:51px">READ MORE</div>
<div class="framed photo" style="left:781px;top:771px;width:310px;height:229px;background:linear-gradient(135deg,#b7a69a,#3a3433 55%,#d8c2b2)" role="img" aria-label="Hands holding a camera lens"></div>
<div class="framed photo" style="left:682px;top:945px;width:300px;height:229px;background:radial-gradient(circle at 45% 45%,#a46a32,#2a160a 40%,#050302 70%)" role="img" aria-label="Couple silhouetted in warm light at night"></div>

<!-- Gallery -->
<section class="gallery"></section>
<h2 class="section-title" style="left:0;width:1200px;text-align:center;top:1380px">GALLERY</h2>
<div class="photo" style="left:111px;top:1465px;width:680px;height:245px;background:linear-gradient(120deg,#6f7a72,#9ea39b 50%,#5d5e58)" role="img" aria-label="Couple relaxing on a sofa by a weathered wall"></div>
<div class="photo" style="left:803px;top:1465px;width:286px;height:245px;background:linear-gradient(135deg,#8b8f70,#d6c7b5 50%,#3a3535)" role="img" aria-label="Bride and groom embracing outdoors"></div>
<div class="photo" style="left:111px;top:1722px;width:288px;height:245px;background:linear-gradient(135deg,#4a3a30,#c9a286 50%,#3a2d28)" role="img" aria-label="Friends toasting with champagne"></div>
<div class="photo" style="left:415px;top:1722px;width:378px;height:245px;background:linear-gradient(180deg,#e7d7b9,#8c7968 60%,#c7b9a9)" role="img" aria-label="Couple dancing in a sunlit courtyard"></div>
<div class="photo" style="left:805px;top:1722px;width:284px;height:245px;background:linear-gradient(135deg,#5b0f18,#b0293a 55%,#6b1420)" role="img" aria-label="Portrait of a woman in a red ruffled dress"></div>
<div class="photo" style="left:111px;top:1979px;width:512px;height:245px;background:linear-gradient(120deg,#6f8a60,#d8b8a0 45%,#3d6670)" role="img" aria-label="Groom placing a ring on the bride's hand"></div>
<div class="photo" style="left:635px;top:1979px;width:454px;height:245px;background:linear-gradient(135deg,#f0f0f0,#dcdcdc)" role="img" aria-label="Couple kissing in front of a white brick wall"></div>
<div class="photo" style="left:111px;top:2240px;width:284px;height:245px;background:radial-gradient(circle at 20% 30%,#d89a3c,#3a2e22 55%,#1f1a16)" role="img" aria-label="Couple smiling with sparkling lights"></div>
<div class="photo" style="left:411px;top:2240px;width:680px;height:245px;background:linear-gradient(180deg,#c9b8a4,#a48d73 45%,#7a6448)" role="img" aria-label="Couple walking hand in hand through a field"></div>

<!-- About Me -->
<section class="about-me"></section>
<div class="abs halo" style="left:200px;top:2700px;width:380px;height:420px;border-radius:50%;background:radial-gradient(circle,#f3d9a8 0%,rgba(241,231,224,0) 70%)"></div>
<div class="framed photo" style="left:111px;top:2724px;width:310px;height:230px;background:linear-gradient(120deg,#8fa3b4,#5d6e7a 50%,#3d2f2a)" role="img" aria-label="Photographer with a camera beside studio lights"></div>
<div class="framed photo" style="left:247px;top:2863px;width:303px;height:229px;background:linear-gradient(120deg,#f2f2f2,#d9d6d2 55%,#5b5a44)" role="img" aria-label="Photographer taking a picture"></div>
<h2 class="section-title" style="left:597px;top:2712px">ABOUT ME</h2>
<p class="body-text" style="left:593px;top:2775px;width:488px">Lorem ipsum dolor sit amet, consectetur adipiscing elit, sed do eiusmod tempor incididunt ut labore et dolore magna aliqua. Ut enim ad minim veniam, quis nostrud exercitation ullamco laboris nisi ut aliquip ex ea commodo consequat. Duis aute irure dolor in reprehenderit in voluptate velit esse cillum dolore eu fugiat nulla pariatur. Excepteur sint occaecat cupidatat non proident, sunt in culpa qui officia deserunt mollit anim id est laborum</p>
<div class="btn" style="left:591px;top:3040px;width:194px;height:52px">READ MORE</div>

<!-- Packages -->
<section class="packages"></section>
<h2 class="section-title" style="left:0;width:1200px;text-align:center;top:3282px">PACKAGES</h2>

<div class="pkg-label" style="left:111px;top:3376px">PACKAGES 1</div>
<div class="photo" style="left:111px;top:3432px;width:308px;height:306px;background:linear-gradient(180deg,#7e8a66,#b79e86 50%,#8a6a4e)" role="img" aria-label="Couple holding a dried flower bouquet"></div>
<div class="price" style="left:186px;top:3760px">$ 350</div>
<p class="pkg-text" style="left:135px;top:3833px">Lorem ipsum dolor sit amet, consectetur adipiscing elit, sed do eiusmod</p>
<div class="btn" style="left:168px;top:3938px;width:194px;height:52px">BOOK NOW</div>

<div class="pkg-label" style="left:443px;top:3376px">PACKAGES 2</div>
<div class="photo" style="left:443px;top:3432px;width:308px;height:306px;background:linear-gradient(180deg,#c99a7c,#d8b19a 40%,#7d6250 70%,#4c3a2c)" role="img" aria-label="Couple walking along a lake shore at sunset"></div>
<div class="price" style="left:518px;top:3760px">$ 525</div>
<p class="pkg-text" style="left:467px;top:3833px">Lorem ipsum dolor sit amet, consectetur adipiscing elit, sed do eiusmod</p>
<div class="btn" style="left:500px;top:3938px;width:194px;height:52px">BOOK NOW</div>

<div class="pkg-label" style="left:769px;top:3376px">PACKAGES 3</div>
<div class="photo" style="left:769px;top:3432px;width:308px;height:306px;background:linear-gradient(135deg,#b8c0c4,#e6e6e4 50%,#3a3c48)" role="img" aria-label="Couple sitting together by a bright window"></div>
<div class="price" style="left:844px;top:3760px">$ 700</div>
<p class="pkg-text" style="left:793px;top:3833px">Lorem ipsum dolor sit amet, consectetur adipiscing elit, sed do eiusmod</p>
<div class="btn" style="left:820px;top:3938px;width:194px;height:52px">BOOK NOW</div>

<!-- Testimonials -->
<section class="testimonials"></section>
<h2 class="section-title" style="left:0;width:1165px;text-align:center;top:4182px">WHAT PEOPLE SAY ABOUT US</h2>
<div class="photo card-bg" role="img" aria-label="Sunset over the sea"></div>
<svg class="abs" style="left:760px;top:4270px" width="110" height="110" viewBox="0 0 110 110"><path d="M110 8 A70 70 0 0 0 40 78" fill="none" stroke="#9c9490" stroke-width="16" opacity=".6"/></svg>
<div class="quote-box">
  <div class="abs" style="left:56px;top:32px;font-size:14px">- THEO</div>
  <div class="abs" style="left:330px;top:26px;font-size:18px;color:var(--gold);letter-spacing:1px">★★★★★</div>
  <p class="abs" style="left:48px;top:72px;width:370px;font-size:14px;line-height:30px;text-align:justify">Sed ut perspiciatis unde omnis iste natus error sit voluptatem accusantium doloremque laudantium, totam rem aperiam, eaque ipsa</p>
</div>
<svg class="abs" style="left:561px;top:4648px" width="40" height="22" viewBox="0 0 40 22"><path d="M0 0 L20 20 L40 0 Z" fill="#9a5a3e"/></svg>
<div class="photo avatar" role="img" aria-label="Portrait of the reviewer"></div>
<div class="abs see-more">SEE MORE
  <svg width="30" height="14" viewBox="0 0 30 14"><path d="M0 7 H26 M20 1 L27 7 L20 13" fill="none" stroke="#2c1a14" stroke-width="2.5"/></svg>
</div>

<!-- Footer -->
<footer class="footer">
  <div class="logo">LUMERA</div>
</footer>
<nav class="footer-nav">
  <a>HOME</a><a style="padding:0 28px">ABOUT PHOTO</a><a>GALLERY</a><a>ABOUT ME</a><a>PACKAGES</a><a style="padding:0 28px">CONTACT US</a>
</nav>
<div class="socials"><span></span><span></span><span></span><span></span><span></span></div>
<div class="copyright">© 2023 Lumera</div>

</body>
</html>
```